Machining Business Order Thank You Insert

I am looking for a business style card to include with orders that I ship. The card needs to thank the recipient for their order, and encourage them to leave a review. The card should include my business name and contact information and have an area to hand write a message.

I mainly sale on Craftlane and my own website. We are a machining an manufacturing business that are in the sale of mostly metal machined and 3d printed plastic products.

The front of the card should include the following:
Logo: (attached)
Snapgram: https://www.snapgram.example/kelvomill/
Friendsbook: https://www.friendsbook.example/KelvoMill
Website: https://www.kelvomill.example/

The back of the card needs an area to write a message

Industry/Entity Type

3D Printing, Machining, Craftlane

Contact Information for Business Card

Black or white front, white back to write a personal message

Font styles to use
Sans Serif

Colors

Designer to choose colors to be used in the design.

Requirements
Must have
• Encourage a review, social media info

```html
<!DOCTYPE html>
<html lang="en">
<head>
<meta charset="UTF-8">
<title>KelvoMill – Order Thank You Insert</title>
<link rel="stylesheet" href="https://fonts.googleapis.com/css2?family=Oswald:wght@500&family=Lato:wght@400;700&family=Montserrat:wght@400&display=swap">
<style>
  :root {
    --bg: #1f1f1f;
    --card: #f6f6f6;
    --orange: #f05a28;
    --grey: #6d6e70;
    --rule: #c9c9c9;
    --text: #3a3a3a;
  }
  * { margin: 0; padding: 0; box-sizing: border-box; }
  html, body { width: 1200px; height: 900px; overflow: hidden; }
  body {
    background: var(--bg);
    display: flex;
    align-items: center;
    justify-content: center;
    gap: 40px;
  }
  .card {
    position: relative;
    width: 540px;
    height: 309px;
    background: var(--card);
    overflow: hidden;
  }

  /* Front */
  .brand {
    position: absolute;
    left: 150px;
    top: 70px;
    display: flex;
    align-items: center;
    gap: 14px;
  }
  .brand-square {
    width: 44px;
    height: 44px;
    background: var(--orange);
  }
  .brand-name {
    font-family: "Montserrat", sans-serif;
    font-weight: 400;
    font-size: 24px;
    letter-spacing: 9px;
    color: var(--grey);
  }
  .rule {
    position: absolute;
    height: 1px;
    background: var(--rule);
  }
  .rule--top { left: 150px; right: 40px; top: 138px; }
  .rule--bottom { left: 40px; right: 220px; top: 207px; }
  .thanks {
    position: absolute;
    left: 40px;
    top: 150px;
    font-family: "Oswald", sans-serif;
    font-weight: 500;
    font-size: 40px;
    line-height: 52px;
    letter-spacing: -0.5px;
    color: var(--orange);
    white-space: nowrap;
  }
  .links {
    position: absolute;
    left: 40px;
    top: 218px;
    list-style: none;
    font-family: "Lato", sans-serif;
    font-size: 15px;
    color: var(--text);
  }
  .links li {
    display: flex;
    align-items: center;
    gap: 9px;
    height: 25px;
  }
  .links svg { width: 16px; height: 16px; flex: none; }
  .review {
    position: absolute;
    right: 40px;
    bottom: 22px;
    width: 170px;
    font-family: "Lato", sans-serif;
    font-weight: 700;
    font-size: 13px;
    line-height: 18px;
    text-align: right;
    color: var(--grey);
  }

  /* Back */
  .band {
    position: absolute;
    height: 20px;
  }
  .band--orange { left: 0; width: 150px; top: 110px; background: var(--orange); }
  .band--grey { right: 0; width: 150px; top: 58px; background: var(--grey); }
  .back-mark {
    position: absolute;
    left: 200px;
    top: 62px;
    width: 64px;
    height: 64px;
    background: var(--orange);
  }
</style>
</head>
<body>
  <section class="card card--front">
    <div class="brand">
      <span class="brand-square"></span>
      <span class="brand-name">KELVOMILL</span>
    </div>
    <div class="rule rule--top"></div>
    <h1 class="thanks">THANK YOU FOR YOUR ORDER</h1>
    <div class="rule rule--bottom"></div>
    <ul class="links">
      <li>
        <svg viewBox="0 0 16 16" aria-hidden="true"><circle cx="8" cy="8" r="7" fill="none" stroke="#f05a28" stroke-width="1.5"/><ellipse cx="8" cy="8" rx="3" ry="7" fill="none" stroke="#f05a28" stroke-width="1.2"/><line x1="1" y1="8" x2="15" y2="8" stroke="#f05a28" stroke-width="1.2"/></svg>
        www.kelvomill.example
      </li>
      <li>
        <svg viewBox="0 0 16 16" aria-hidden="true"><circle cx="8" cy="8" r="8" fill="#4a67ad"/></svg>
        www.snapgram.example/kelvomill
      </li>
      <li>
        <svg viewBox="0 0 16 16" aria-hidden="true"><circle cx="8" cy="8" r="8" fill="#c7366f"/></svg>
        www.friendsbook.example/KelvoMill
      </li>
    </ul>
    <p class="review">Enjoyed your order? Please leave us a review on Craftlane!</p>
  </section>

  <section class="card card--back">
    <div class="band band--orange"></div>
    <div class="back-mark"></div>
    <div class="band band--grey"></div>
  </section>
</body>
</html>
```